Business Card for Canvas Calm-Eco Friendly Organic Clothing Brand

We are looking for an amazing business card for our eco friendly, organic clothing brand. We are thinking maybe a business card with a peel off sticker on the back, since our hanging clothing tag is a peel off sticker on the back. I will attach our hang tag so we can make sure we stay in line with our design. I've also attached a bag we are doing because I do like the scattered emblem look as well.

```html
<!DOCTYPE html>
<html lang="en">
<head>
<meta charset="utf-8">
<title>Canvas Calm Business Card</title>
<link href="https://fonts.googleapis.com/css2?family=Arimo:wght@400;700&display=swap" rel="stylesheet">
<style>
  :root {
    --page-bg: #e4e1da;
    --card-white: #ffffff;
    --card-black: #121212;
    --gold: #d8a92c;
    --gold-light: #f2cf5b;
    --text-light: #f1f1f1;
    --tag-green: #1e2416;
    --tag-green-light: #3a4526;
    --camo-dark: #5d5a1f;
    --camo-mid: #a8962e;
    --camo-light: #e8c94a;
  }
  * { box-sizing: border-box; margin: 0; padding: 0; }
  html, body {
    width: 1200px; height: 950px; overflow: hidden;
    background: var(--page-bg);
    font-family: "Arimo", Arial, sans-serif;
  }
  .card {
    position: absolute;
    width: 600px; height: 343px;
    border-radius: 22px;
    box-shadow: 0 10px 30px rgba(0,0,0,0.18);
  }

  /* Back side */
  .card-back { left: 300px; top: 80px; background: var(--card-white); }
  .brand-tag {
    position: absolute; left: 170px; top: 126px;
    width: 290px; height: 92px;
    background: linear-gradient(135deg, var(--tag-green-light), var(--tag-green));
    border-radius: 14px;
    border: 2px solid var(--gold);
  }
  .brand-tag .tag-emblem {
    position: absolute; left: -38px; top: -14px;
    width: 84px; height: 84px;
    transform: rotate(45deg);
    background: var(--tag-green);
    border: 2px solid var(--gold);
  }
  .brand-tag .tag-emblem .figure-art {
    position: absolute; inset: 10px;
    transform: rotate(-45deg);
    background: radial-gradient(circle at 45% 40%, var(--camo-light), var(--camo-mid) 55%, var(--camo-dark));
    border-radius: 40% 40% 30% 30%;
  }
  .brand-tag .tag-name {
    position: absolute; left: 72px; top: 22px;
    font-size: 30px; font-weight: 700;
    color: var(--gold-light);
    letter-spacing: 0.5px;
  }
  .brand-tag .tag-web {
    position: absolute; left: 74px; top: 62px;
    font-size: 11px; color: var(--text-light);
  }

  /* Front side */
  .card-front { left: 300px; top: 510px; background: var(--card-white); }
  .front-panel {
    position: absolute; inset: 10px;
    background: var(--card-black);
    border-radius: 16px;
  }
  .front-frame {
    position: absolute; inset: 12px;
    border: 2px solid var(--gold);
    border-radius: 12px;
  }
  .emblem-diamond {
    position: absolute; left: 50px; top: 48px;
    width: 190px; height: 190px;
    transform: rotate(45deg);
    background: var(--card-black);
    border: 3px solid var(--gold);
    box-shadow: 0 0 0 3px var(--card-black), 0 0 0 5px var(--gold);
  }
  .emblem-diamond .figure-art {
    position: absolute; inset: 32px;
    transform: rotate(-45deg);
    background: radial-gradient(circle at 45% 35%, var(--camo-light), var(--camo-mid) 50%, var(--camo-dark));
    border-radius: 45% 45% 30% 30%;
  }
  .contact {
    position: absolute; left: 330px; top: 110px;
    color: var(--text-light);
    font-size: 16px; line-height: 22px;
  }
  .contact .name { color: var(--gold); font-size: 21px; line-height: 26px; }
  .contact .role { margin-bottom: 14px; }
  .contact .line { display: flex; align-items: center; gap: 8px; }
  .contact .line svg { width: 15px; height: 15px; flex: none; }
  .tag-hole {
    position: absolute; right: 30px; top: 160px;
    width: 18px; height: 18px; border-radius: 50%;
    background: var(--card-white);
  }
</style>
</head>
<body>

<section class="card card-back" aria-label="Card back">
  <div class="brand-tag">
    <div class="tag-emblem"><div class="figure-art" role="img" aria-label="Camouflage meditating figure emblem"></div></div>
    <div class="tag-name">Canvas Calm</div>
    <div class="tag-web">www.canvascalm.com</div>
  </div>
</section>

<section class="card card-front" aria-label="Card front">
  <div class="front-panel"></div>
  <div class="front-frame"></div>
  <div class="emblem-diamond"><div class="figure-art" role="img" aria-label="Camouflage meditating figure emblem"></div></div>
  <div class="contact">
    <div class="name">Alan Reyes</div>
    <div class="role">President</div>
    <div class="address">142 Orchard Lane</div>
    <div class="address">Maple Grove, NY 11020</div>
    <div class="line">
      <svg viewBox="0 0 16 16" fill="var(--gold)" aria-hidden="true"><path d="M2 5c0-2 2-3 6-3s6 1 6 3v1h-3V5H5v1H2z M4 7h8l2 7H2z"/></svg>
      <span>555 0142 7781</span>
    </div>
    <div class="line">
      <svg viewBox="0 0 16 16" fill="var(--gold)" aria-hidden="true"><rect x="4" y="1" width="8" height="14" rx="1.5"/><rect x="5.5" y="3" width="5" height="8" fill="var(--card-black)"/></svg>
      <span>555 0198 3364</span>
    </div>
    <div class="line">
      <svg viewBox="0 0 16 16" fill="var(--gold)" aria-hidden="true"><rect x="4" y="1" width="8" height="5"/><rect x="1" y="6" width="14" height="6" rx="1"/><rect x="4" y="10" width="8" height="5"/></svg>
      <span>555 0176 2209</span>
    </div>
    <div class="line">
      <svg viewBox="0 0 16 16" aria-hidden="true"><rect x="1" y="3" width="14" height="10" fill="var(--gold)"/><path d="M1 3l7 6 7-6" fill="none" stroke="var(--card-black)" stroke-width="1.4"/></svg>
      <span>hello@canvascalm.com</span>
    </div>
  </div>
  <div class="tag-hole"></div>
</section>

</body>
</html>
```